Lumen Fitness Personal Training Business

I need a business card design with a logo for my personal training company. I'd like the colors to be a vibrant green and black. I'd like the logo to incorporate an anvil (or something similar). I train hardcore competitive athletes as well as soccer moms trying to get and/or stay in shape. I need a logo that will not pigeon hole me in one category or the other, but at the same time not be too intimidating to soccer moms, but will not be off putting to the more hardcore trainees. The design should be attention grabbing and aesthetic.
Target Market(s)
Hardcore athletes as well as average people just trying to get/stay in shape.
Industry/Entity Type
Training

```html
<!DOCTYPE html>
<html lang="en">
<head>
<meta charset="utf-8">
<title>Lumen Fitness – Business Card</title>
<link rel="stylesheet" href="https://fonts.googleapis.com/css2?family=Lato:wght@400;700;900&display=swap">
<style>
  :root {
    --stage: #3a332f;
    --card: #1a1a1a;
    --card-deep: #121212;
    --green: #3fc04f;
    --green-dark: #1f9a35;
    --white: #f2f2f2;
    --grey: #a8a8a8;
    --grey-dim: #7d7d7d;
  }
  * { box-sizing: border-box; margin: 0; padding: 0; }
  html, body {
    width: 1200px;
    height: 844px;
    overflow: hidden;
    background: var(--stage);
    font-family: "Lato", sans-serif;
  }
  .stage {
    position: relative;
    width: 1200px;
    height: 844px;
    display: flex;
    align-items: center;
    justify-content: center;
    gap: 60px;
  }
  .card {
    position: relative;
    width: 525px;
    height: 300px;
    background: linear-gradient(135deg, var(--card) 0%, var(--card-deep) 100%);
    overflow: hidden;
    box-shadow: 0 6px 18px rgba(0,0,0,.35);
  }

  /* Contact side */
  .band {
    position: absolute;
    left: 0;
    width: 100%;
  }
  .band--top { top: 16px; height: 14px; background: var(--green); }
  .band--top::after {
    content: ""; position: absolute; left: 0; bottom: -5px;
    width: 100%; height: 5px; background: var(--green-dark);
  }
  .band--bottom { bottom: 16px; height: 14px; background: var(--green); }
  .band--bottom::before {
    content: ""; position: absolute; left: 0; top: -5px;
    width: 100%; height: 5px; background: var(--green-dark);
  }
  .contact {
    position: absolute;
    inset: 60px 0 50px 0;
    display: flex;
    flex-direction: column;
    align-items: center;
    text-align: center;
  }
  .contact__name {
    color: var(--white);
    font-size: 20px;
    font-weight: 400;
    letter-spacing: 0.5px;
    text-transform: uppercase;
    padding-bottom: 3px;
    border-bottom: 2px solid var(--green-dark);
  }
  .contact__role {
    color: var(--grey-dim);
    font-size: 15px;
    margin-top: 4px;
  }
  .contact__lines {
    list-style: none;
    margin-top: 28px;
    color: var(--grey);
    font-size: 15px;
    line-height: 1.3;
  }
  .contact__address {
    margin-top: 22px;
    color: var(--grey);
    font-size: 15px;
  }

  /* Logo side */
  .tab {
    position: absolute;
    width: 26px;
    height: 44px;
    background: var(--green);
    border-left: 5px solid var(--green-dark);
  }
  .tab--left { left: 0; top: 150px; }
  .tab--right { right: 0; top: 30px; }
  .brand {
    position: absolute;
    inset: 0;
    display: flex;
    align-items: center;
    justify-content: center;
    gap: 14px;
  }
  .brand__mark {
    width: 26px;
    height: 26px;
    background: var(--green);
  }
  .brand__name {
    color: var(--green);
    font-size: 40px;
    font-weight: 900;
    text-transform: uppercase;
    letter-spacing: 0.5px;
  }
</style>
</head>
<body>
  <main class="stage">
    <section class="card card--contact" aria-label="Card back with contact details">
      <div class="band band--top"></div>
      <div class="contact">
        <h1 class="contact__name">Marcus Hale</h1>
        <p class="contact__role">Managing Director</p>
        <ul class="contact__lines">
          <li>044-555-0142</li>
          <li>123-555-0198</li>
          <li>hello@lumenfitness.example</li>
          <li>www.lumenfitness.example</li>
        </ul>
        <p class="contact__address">1234 Ridge Road | Country Name, AB | 123456</p>
      </div>
      <div class="band band--bottom"></div>
    </section>

    <section class="card card--brand" aria-label="Card front with brand name">
      <div class="tab tab--right"></div>
      <div class="tab tab--left"></div>
      <div class="brand">
        <span class="brand__mark"></span>
        <span class="brand__name">Lumen Fitness</span>
      </div>
    </section>
  </main>
</body>
</html>
```